Tandem Pocket Apps Needs banners for webpage

We need a top banner. We are a mobile app developer for the Hospitality Industry. We are developing a Loyalty Program with the trade name TandemPerks. The banner will be used on our loyalty page inside our website.Please see www.tandempocketapps.example to understand our theme. The banner should be 1700 X 470.

Please see the attached banner. This is from a competitor website.Please use it as a model and make changes...... make it unique to TandemPocket. I need to convey the same message as this banner. Same statistics. Same setting (restaurant).

I have added a purchased vector file for the restaurant setting. I noticed many are struggling and using stock art which I don't like.Work with the background color. Make it more playful--pastels--less formal. Be creative!

Do not wait till that last day of the contest to submit. I might take the first design I like and proceed. The sooner you post a design, the better direction I can give you.
Updates

Project Deadline Extended
Reason: Not getting any designs I can work with yet. Please give me ideas.

All, Please re-read the brief. I have changed the banner project. It will be much easier but I need it quickly.

Now that I have made this banner much easier, I would like to wrap this contest up. Don't wait till the last day to post designs. The first design I like I will go with and close the project. Be creative, colorful, imaginative! Good luck. Marcus Hennet Tandem Pocket Apps, LLC mhennet@

All. See the vector file that I just purchased for the background image. Can you try different background colors. I still need the other content showing the percentages of loyalty. I do not want the rocket ship!

All, I have updated the brief. I have included a vector file that has a perfect restaurant scene. Please be creative and work with colors in this scene. Also be creative with the information in the circles showing the metrics of loyalty. Do not use the Rocket. If you find another idea to replace the rocket, that's fine. Or, just leave it off. Please make this banner unique!

Target Market(s)

Hospitality Industry.

Industry/Entity Type

Restaurant

Requirements
Must have
• Banner should be beautiful.. Image of diners at restaurant along with the statistics and message "Boost Sales".
Nice to have
• Our banner should convey the same message as the attached but we must re-design because the attached banner belongs to another company.
Should not have
• Do not re-use any of the images in the attached banner. This is from my competitor. Do not use a rocket for "Boost Sales" image.

```html
<!DOCTYPE html>
<html lang="en">
<head>
<meta charset="utf-8">
<title>TandemPerks – Boost Sales</title>
<link rel="stylesheet" href="https://fonts.googleapis.com/css2?family=Mulish:wght@400;600;700&family=Prata&display=swap">
<style>
  :root {
    --magenta: #cc0058;
    --magenta-deep: #8a0036;
    --shadow: #3a0016;
    --coral: #fb4a6f;
    --wine: #4a0020;
    --plum: #2b0512;
    --pink-soft: #f25f85;
    --pink-text: #ff6e96;
    --white: #ffffff;
  }
  * { margin: 0; padding: 0; box-sizing: border-box; }
  html, body { width: 1200px; height: 331px; overflow: hidden; background: var(--magenta); }
  .banner {
    position: relative;
    width: 1200px;
    height: 331px;
    overflow: hidden;
    font-family: "Mulish", sans-serif;
  }
  .scene {
    position: absolute;
    inset: 0;
    background:
      radial-gradient(ellipse 260px 150px at 170px 120px, var(--shadow) 0%, rgba(58,0,22,0) 75%),
      radial-gradient(ellipse 240px 160px at 1010px 110px, var(--shadow) 0%, rgba(58,0,22,0) 75%),
      radial-gradient(ellipse 500px 140px at 600px 230px, rgba(90,0,35,.55) 0%, rgba(90,0,35,0) 80%),
      linear-gradient(180deg, var(--magenta) 0%, var(--magenta) 70%, var(--magenta-deep) 100%);
  }
  .headline {
    position: absolute;
    left: 420px;
    top: -4px;
    width: 332px;
    height: 108px;
  }
  .headline svg { position: absolute; inset: 0; }
  .headline-title {
    position: absolute;
    top: 8px;
    width: 100%;
    text-align: center;
    color: var(--white);
    font-weight: 700;
    font-size: 29px;
    letter-spacing: .2px;
  }
  .headline-sub {
    position: absolute;
    top: 44px;
    width: 100%;
    text-align: center;
    color: var(--pink-text);
    font-size: 10px;
  }
  .stat {
    position: absolute;
    top: 110px;
    width: 192px;
    height: 192px;
    border-radius: 50%;
    border: 7px solid var(--white);
    box-shadow: 0 0 0 1px rgba(255,255,255,.4);
    display: flex;
    flex-direction: column;
    align-items: center;
    justify-content: center;
    text-align: center;
  }
  .stat-visits { left: 274px; background: var(--coral); color: var(--wine); }
  .stat-spend  { left: 498px; background: var(--wine); color: var(--pink-text); }
  .stat-ratio  { left: 725px; background: var(--plum); color: var(--white); }
  .stat-lead { font-size: 10.5px; font-weight: 600; line-height: 1.2; }
  .stat-about { font-size: 13.5px; font-weight: 600; }
  .stat-figure {
    font-family: "Prata", serif;
    font-size: 38px;
    line-height: 1.2;
    color: var(--white);
    margin: 2px 0 2px 14px;
  }
  .stat-compare { font-size: 10px; font-weight: 600; }
  .stat-base { font-size: 11px; font-weight: 600; margin-top: 2px; }
  .stat-visits .stat-base { color: var(--white); }
  .ratio-icons { width: 128px; height: 50px; margin-top: 6px; }
  .ratio-label { font-size: 10px; font-weight: 600; margin-top: 14px; }
  .ratio-base { font-size: 11.5px; font-weight: 700; margin-top: 2px; }
</style>
</head>
<body>
<div class="banner">
  <div class="scene" role="img" aria-label="Silhouetted diners seated at tables in a restaurant, in magenta tones"></div>

  <header class="headline">
    <svg viewBox="0 0 332 108" width="332" height="108" aria-hidden="true">
      <path d="M0,2 C20,2 30,10 30,28 L30,46 C30,66 48,76 88,76 L138,76 C158,76 166,90 166,106 C166,90 174,76 194,76 L244,76 C284,76 302,66 302,46 L302,28 C302,10 312,2 332,2 Z"
            fill="var(--wine)" stroke="var(--white)" stroke-width="4"/>
    </svg>
    <h1 class="headline-title">Boost Sales</h1>
    <p class="headline-sub">Vivamus porttitor purus nisi eleifend</p>
  </header>

  <section class="stat stat-visits">
    <p class="stat-lead">LOYAL GUESTS VISIT</p>
    <p class="stat-about">ABOUT</p>
    <p class="stat-figure">32%</p>
    <p class="stat-compare">MORE THAN</p>
    <p class="stat-base">Average guests</p>
  </section>

  <section class="stat stat-spend">
    <p class="stat-lead">LOYAL GUESTS SPEND</p>
    <p class="stat-about">ABOUT</p>
    <p class="stat-figure">25%</p>
    <p class="stat-compare">MORE THAN</p>
    <p class="stat-base">Average guests</p>
  </section>

  <section class="stat stat-ratio">
    <svg class="ratio-icons" viewBox="0 0 128 50" aria-hidden="true" fill="var(--pink-soft)">
      <circle cx="22" cy="13" r="11"/>
      <path d="M0,50 C0,34 8,27 22,27 C36,27 44,34 44,50 Z"/>
      <path d="M22,27 L19,31 L22,44 L25,31 Z" fill="var(--plum)"/>
      <path d="M56,22 L61,27 L56,32 M61,22 L66,27 L61,32" fill="none" stroke="var(--pink-soft)" stroke-width="1.5"/>
      <circle cx="86" cy="22" r="6"/>
      <path d="M76,44 C76,35 80,31 86,31 C92,31 96,35 96,44 Z"/>
      <circle cx="118" cy="22" r="6"/>
      <path d="M108,44 C108,35 112,31 118,31 C124,31 128,35 128,44 Z"/>
      <circle cx="102" cy="17" r="8" stroke="var(--plum)" stroke-width="1.5"/>
      <path d="M88,48 C88,36 94,29 102,29 C110,29 116,36 116,48 Z" stroke="var(--plum)" stroke-width="1.5"/>
    </svg>
    <p class="ratio-label">Loyal Guest = 1</p>
    <p class="ratio-base">Average Guest 10</p>
  </section>
</div>
</body>
</html>
```